Stonebridge Building and Projects business cards

A business card with watermark background (construction work)

Company logo attached

Home improvement projects
House renovations
Bathroom and kitchen renovations
House extensions
New builds and granny flats

Director Omar Haddani
(Phone number)
omar@sbpbuilding.com.au
(Instagram logo) sbp_building

```html
<!DOCTYPE html>
<html lang="en">
<head>
<meta charset="utf-8">
<title>Stonebridge Building and Projects – Business Cards</title>
<link rel="stylesheet" href="https://fonts.googleapis.com/css2?family=Montserrat:wght@700&family=Roboto:wght@400;500;700&display=swap">
<style>
  :root {
    --stage: #2b2b2d;
    --brand-blue: #1b74c4;
    --brand-blue-deep: #135a9c;
    --band-grey: #3b3d41;
    --paper: #f4f4f4;
    --paper-shade: #e6e6e6;
    --ink: #3a3a3a;
    --ink-soft: #555;
    --white: #ffffff;
  }
  * { box-sizing: border-box; margin: 0; padding: 0; }
  html, body { width: 1200px; height: 1050px; overflow: hidden; }
  body {
    background: var(--stage);
    font-family: "Roboto", Arial, sans-serif;
    position: relative;
  }
  .card {
    position: absolute;
    left: 220px;
    width: 760px;
    height: 434px;
    border-radius: 34px;
    overflow: hidden;
    box-shadow: 0 14px 30px rgba(0,0,0,.45);
  }
  /* ---------- front ---------- */
  .card--front {
    top: 58px;
    background: linear-gradient(135deg, var(--brand-blue) 0%, var(--brand-blue-deep) 100%);
    color: var(--white);
  }
  .front-brand {
    position: absolute;
    top: 70px; left: 0; right: 0;
    display: flex; align-items: center; justify-content: center; gap: 18px;
  }
  .brand-square {
    width: 26px; height: 26px; background: currentColor; flex: none;
  }
  .brand-name {
    font-family: "Montserrat", Arial, sans-serif;
    font-weight: 700;
    font-size: 38px;
    line-height: 1.15;
  }
  .service-band {
    position: absolute;
    left: 0; right: 0; top: 222px; height: 118px;
    background: var(--band-grey);
    display: flex; flex-direction: column; justify-content: center; align-items: center;
    gap: 8px;
    font-size: 19px;
  }
  .service-band .sep { opacity: .8; margin: 0 10px; }
  .front-contacts {
    position: absolute;
    left: 0; right: 0; top: 362px;
    display: flex; justify-content: center; gap: 46px;
    font-size: 19px;
  }
  .contact { display: flex; align-items: center; gap: 10px; }
  .contact svg { width: 20px; height: 20px; flex: none; }
  /* ---------- back ---------- */
  .card--back {
    top: 554px;
    background: var(--paper);
  }
  .back-watermark {
    position: absolute;
    right: 0; top: 0; width: 430px; height: 434px;
    background: linear-gradient(160deg, rgba(0,0,0,0) 0%, var(--paper-shade) 55%, rgba(0,0,0,0) 100%);
  }
  .back-brand {
    position: absolute;
    left: 48px; top: 170px; width: 300px;
    display: flex; align-items: center; gap: 14px;
    color: var(--brand-blue);
  }
  .back-brand .brand-name { font-size: 30px; }
  .back-brand .brand-square { width: 22px; height: 22px; }
  .person {
    position: absolute;
    left: 420px; top: 70px;
  }
  .person-name {
    font-size: 28px; font-weight: 700; color: var(--brand-blue);
  }
  .person-role {
    font-size: 18px; color: var(--ink-soft); margin-top: 4px;
  }
  .back-contacts {
    list-style: none;
    margin-top: 26px;
    display: flex; flex-direction: column; gap: 10px;
    font-size: 18px; color: var(--ink);
  }
  .back-contacts .contact svg { color: var(--brand-blue); }
</style>
</head>
<body>

<section class="card card--front" aria-label="Card front">
  <div class="front-brand">
    <span class="brand-square"></span>
    <span class="brand-name">Stonebridge Building<br>and Projects</span>
  </div>

  <div class="service-band">
    <p>Home Improvement Projects<span class="sep">|</span>House Renovations<span class="sep">|</span>House Extensions</p>
    <p>Bathroom &amp; Kitchen Renovations<span class="sep">|</span>New Builds &amp; Granny Flats</p>
  </div>

  <div class="front-contacts">
    <span class="contact">
      <svg viewBox="0 0 20 20"><circle cx="10" cy="10" r="9" fill="currentColor"/></svg>
      sbp_building
    </span>
    <span class="contact">
      <svg viewBox="0 0 20 20" fill="none" stroke="currentColor" stroke-width="1.6">
        <circle cx="10" cy="10" r="8.2"/><ellipse cx="10" cy="10" rx="3.6" ry="8.2"/><path d="M2 10h16M3.5 6h13M3.5 14h13"/>
      </svg>
      sbpbuilding.com.au
    </span>
  </div>
</section>

<section class="card card--back" aria-label="Card back">
  <div class="back-watermark" role="img" aria-label="Faint construction work background"></div>

  <div class="back-brand">
    <span class="brand-square"></span>
    <span class="brand-name">Stonebridge Building and Projects</span>
  </div>

  <div class="person">
    <h1 class="person-name">Omar Haddani</h1>
    <p class="person-role">Managing Director</p>
    <ul class="back-contacts">
      <li class="contact">
        <svg viewBox="0 0 20 20" fill="none" stroke="currentColor" stroke-width="1.6">
          <circle cx="10" cy="10" r="8.2"/><path d="M7 5.8l1.6 2.4-1 1.1c.6 1.3 1.5 2.2 2.8 2.8l1.1-1 2.4 1.6-.9 1.6c-3.6-.3-6.6-3.3-6.9-6.9z" fill="currentColor" stroke="none"/>
        </svg>
        0400 123 987
      </li>
      <li class="contact">
        <svg viewBox="0 0 20 20" fill="none" stroke="currentColor" stroke-width="1.6">
          <rect x="2" y="4.5" width="16" height="11" rx="1.5"/><path d="M2.5 5.5L10 11l7.5-5.5"/>
        </svg>
        omar@sbpbuilding.com.au
      </li>
      <li class="contact">
        <svg viewBox="0 0 20 20" fill="none" stroke="currentColor" stroke-width="1.6">
          <circle cx="10" cy="10" r="8.2"/><ellipse cx="10" cy="10" rx="3.6" ry="8.2"/><path d="M2 10h16M3.5 6h13M3.5 14h13"/>
        </svg>
        sbpbuilding.com.au
      </li>
      <li class="contact">
        <svg viewBox="0 0 20 20"><circle cx="10" cy="10" r="9" fill="currentColor"/></svg>
        sbp_building
      </li>
    </ul>
  </div>
</section>

</body>
</html>
```